Request for Business Card Design

Hi. My name is Marlene, I am looking for a new business card design for my company, Quarrow Signal Instruments, LLC. I really like the design you did for Tarsel Venture and was hoping you could do something similar using our full logo and our mark. I am also open to any raised texture design using our mark. I have attached our full logo, which would need to be somewhere on the card, as well as the mark in both outline and full form, as well as our brand colors / guide. The card does not have to be white, as long as our logo and mark appear. I actually like darker colored business cards more, but am open to all options. If you are interested in working with me, please let me know. We would also take the business card design into letterhead design if you can do that.

```html
<!DOCTYPE html>
<html lang="en">
<head>
<meta charset="utf-8">
<title>Quarrow Signal Instruments – Business Card</title>
<link href="https://fonts.googleapis.com/css2?family=Open+Sans:wght@400;600;700;800&display=swap" rel="stylesheet">
<style>
  :root {
    --backdrop: #4a423d;
    --card: #171717;
    --accent: #0e9ac1;
    --ink: #ffffff;
    --ink-soft: #e6e6e6;
  }
  * { margin: 0; padding: 0; box-sizing: border-box; }
  html, body {
    width: 1200px; height: 716px; overflow: hidden;
    background: var(--backdrop);
    font-family: "Open Sans", Arial, sans-serif;
  }
  .stage { position: relative; width: 1200px; height: 716px; }

  .card {
    position: absolute; top: 203px;
    width: 540px; height: 310px;
    background: var(--card);
    overflow: hidden;
    box-shadow: 0 10px 28px rgba(0,0,0,.45);
  }
  .card--front { left: 50px; }
  .card--back  { left: 610px; }

  .card__disc { position: absolute; top: 0; width: 540px; height: 310px; }
  .card__disc circle { fill: var(--accent); }

  .brand { position: absolute; display: flex; align-items: center; gap: 12px; }
  .brand__dot { width: 30px; height: 30px; border-radius: 50%; background: var(--accent); flex: none; }
  .brand__name {
    color: var(--ink); font-weight: 800; font-size: 17px;
    letter-spacing: .06em; line-height: 1.2; text-transform: uppercase;
  }
  .card--front .brand { left: 40px; top: 60px; }
  .card--back .brand { right: 40px; top: 42px; }
  .card--back .brand__name { text-align: right; }

  .contact {
    position: absolute; right: 48px; top: 128px;
    text-align: right; color: var(--ink-soft);
  }
  .contact__name {
    color: var(--accent); font-weight: 700; font-size: 21px;
    letter-spacing: .02em; text-transform: uppercase; line-height: 1.1;
  }
  .contact__role { font-size: 15px; margin-top: 2px; }
  .contact__address { font-size: 14px; line-height: 1.35; margin-top: 12px; }
  .contact__lines { list-style: none; margin-top: 10px; font-size: 14px; line-height: 1.55; }
  .contact__lines li { display: flex; justify-content: flex-end; align-items: center; gap: 8px; }
  .contact__lines svg { width: 13px; height: 13px; fill: var(--accent); flex: none; }

  .edge-bar {
    position: absolute; right: 0; top: 130px;
    width: 14px; height: 52px; background: var(--accent);
  }
</style>
</head>
<body>
<main class="stage">

  <section class="card card--front">
    <svg class="card__disc" viewBox="0 0 540 310" aria-hidden="true">
      <circle cx="560" cy="170" r="150"/>
    </svg>
    <div class="brand">
      <span class="brand__dot"></span>
      <span class="brand__name">Quarrow<br>Signal Instruments</span>
    </div>
  </section>

  <section class="card card--back">
    <svg class="card__disc" viewBox="0 0 540 310" aria-hidden="true">
      <circle cx="0" cy="170" r="150"/>
    </svg>
    <div class="brand">
      <span class="brand__dot"></span>
      <span class="brand__name">Quarrow<br>Signal Instruments</span>
    </div>

    <div class="contact">
      <h1 class="contact__name">Dara Whitcombe</h1>
      <p class="contact__role">Managing Director</p>
      <p class="contact__address">Your address, City<br>State, Zip 1234</p>
      <ul class="contact__lines">
        <li>123 456 789
          <svg viewBox="0 0 24 24"><path d="M6.6 10.8a15.1 15.1 0 0 0 6.6 6.6l2.2-2.2a1 1 0 0 1 1-.25 11.4 11.4 0 0 0 3.6.57 1 1 0 0 1 1 1V20a1 1 0 0 1-1 1A17 17 0 0 1 3 4a1 1 0 0 1 1-1h3.5a1 1 0 0 1 1 1c0 1.25.2 2.45.57 3.57a1 1 0 0 1-.25 1z"/></svg>
        </li>
        <li>info@youremail.com
          <svg viewBox="0 0 24 24"><path d="M2 5h20v14H2z M2 5l10 8 10-8" fill="none" stroke="#0e9ac1" stroke-width="2"/></svg>
        </li>
        <li>www.yourwebsite.com
          <svg viewBox="0 0 24 24"><circle cx="12" cy="12" r="9" fill="none" stroke="#0e9ac1" stroke-width="2"/><path d="M3 12h18M12 3c3 3 3 15 0 18M12 3c-3 3-3 15 0 18" fill="none" stroke="#0e9ac1" stroke-width="1.6"/></svg>
        </li>
      </ul>
    </div>
    <div class="edge-bar"></div>
  </section>

</main>
</body>
</html>
```